Business Card Design For Office Furniture Clearance Company

Kestrel Office Clearance - our company name pretty much explains what we do, we clear offices for high end clients, mainly plc's and large international companies.

We require a nice looking business card that displays professionalism but without being too serious.

It would be nice to see just a little more than a conventional boring business card, make sure you add some flare.

Industry/Entity Type

Office Furniture

Contact Information for Business Card

CARD 1

Mark Holloway
Director
mark@kestrelofficeclearance.co.uk
m: 07700 153928

t: 01632 960418
www.kestrelofficeclearance.co.uk

Kestrel Office Clearance
Unit K4 B
2-8 Fenwick Lane
Harlow Vale
Northbridge
ZZ9 4QT

free office clearances… you cant get better than that.

CARD 2

Peter Radford
Director
peter@kestrelofficeclearance.co.uk
m: 07700 382615

t: 01632 960418

Kestrel Office Clearance
Unit K4 B
2-8 Fenwick Lane
Harlow Vale
Northbridge
ZZ9 4QT

Font styles to use
Sans Serif

Requirements
Must have
• A white background - as we have a blue logo.
Nice to have
• Nice use of the logo - play around with this and dissect it.

```html
<!DOCTYPE html>
<html lang="en">
<head>
<meta charset="utf-8">
<title>Kestrel Office Clearance – Business Card</title>
<link rel="stylesheet" href="https://fonts.googleapis.com/css2?family=Lato:wght@400;700&display=swap">
<style>
  :root {
    --brand-blue: #0a7bc0;
    --brand-dark: #07609e;
    --card-white: #f5f4f4;
    --text-white: #ffffff;
    --page-bg: #e6e6e6;
  }
  * { margin: 0; padding: 0; box-sizing: border-box; }
  html, body { width: 1138px; height: 1200px; overflow: hidden; }
  body {
    background: var(--page-bg);
    font-family: "Lato", sans-serif;
    position: relative;
  }
  .card {
    position: absolute;
    width: 670px;
    height: 384px;
    border-radius: 14px;
    overflow: hidden;
    background: var(--brand-blue);
    box-shadow: 0 2px 6px rgba(0,0,0,0.15);
  }
  .card-front { left: 218px; top: 198px; }
  .card-back  { left: 218px; top: 617px; }
  .card-front .shape { position: absolute; inset: 0; }
  .brand-block {
    position: absolute;
    left: 0; top: 0;
    width: 316px;
    text-align: center;
  }
  .brand-dot {
    position: absolute;
    left: 91px; top: 110px;
    width: 136px; height: 136px;
    border-radius: 50%;
    background: var(--brand-blue);
  }
  .brand-name {
    position: absolute;
    left: 0; top: 253px;
    width: 318px;
    color: var(--brand-blue);
    font-weight: 700;
    font-size: 22px;
    white-space: nowrap;
  }
  .contact {
    position: absolute;
    left: 374px; top: 66px;
    color: var(--text-white);
  }
  .contact .name { font-size: 25px; font-weight: 700; line-height: 1.1; }
  .contact .role { font-size: 15.5px; line-height: 1.2; }
  .contact .address { margin-top: 45px; font-size: 16px; line-height: 19.5px; }
  .contact .lines { margin-top: 19px; list-style: none; font-size: 15.5px; }
  .contact .lines li { display: flex; align-items: center; height: 21.5px; white-space: nowrap; }
  .contact .lines svg { width: 16px; height: 16px; margin-right: 8px; flex: none; }
  .back-name {
    position: absolute;
    left: 0; top: 150px; width: 100%;
    text-align: center;
    color: var(--text-white);
    font-weight: 700;
    font-size: 44px;
  }
  .back-web {
    position: absolute;
    left: 0; top: 340px; width: 100%;
    text-align: center;
    color: var(--text-white);
    font-size: 16px;
  }
</style>
</head>
<body>
  <section class="card card-front">
    <svg class="shape" viewBox="0 0 670 384" width="670" height="384">
      <path d="M254,0 Q384,192 250,384 L276,384 Q398,200 262,0 Z" fill="var(--brand-dark)"/>
      <path d="M264,0 Q402,200 280,384" fill="none" stroke="#ffffff" stroke-width="2"/>
      <path d="M0,0 L254,0 Q384,192 250,384 L0,384 Z" fill="var(--card-white)"/>
    </svg>
    <div class="brand-block">
      <div class="brand-dot"></div>
      <div class="brand-name">Kestrel Office Clearance</div>
    </div>
    <div class="contact">
      <div class="name">Mark Holloway</div>
      <div class="role">Director</div>
      <div class="address">Unit K4 B, 2-8 Fenwick Lane<br>Harlow Vale, Northbridge<br>ZZ9 4QT</div>
      <ul class="lines">
        <li><svg viewBox="0 0 16 16"><rect x="4" y="1" width="8" height="14" rx="1.5" fill="none" stroke="#fff" stroke-width="1.4"/><circle cx="8" cy="12.5" r="0.9" fill="#fff"/></svg>07700 153928</li>
        <li><svg viewBox="0 0 16 16"><path d="M3 1.5 L6 1.5 L7 5 L5.2 6.4 Q6.6 9.4 9.6 10.8 L11 9 L14.5 10 L14.5 13 Q14.5 14.5 13 14.5 Q3.5 13.5 1.5 3 Q1.5 1.5 3 1.5 Z" fill="#fff"/></svg>01632 960418</li>
        <li><svg viewBox="0 0 16 16"><rect x="1" y="3.5" width="14" height="9" fill="none" stroke="#fff" stroke-width="1.3"/><path d="M1 3.5 L8 9 L15 3.5" fill="none" stroke="#fff" stroke-width="1.3"/></svg>mark@kestrelofficeclearance.co.uk</li>
        <li><svg viewBox="0 0 16 16"><g fill="none" stroke="#fff" stroke-width="1.2"><circle cx="8" cy="8" r="6.5"/><ellipse cx="8" cy="8" rx="3" ry="6.5"/><path d="M1.5 8 H14.5 M2.5 4.8 H13.5 M2.5 11.2 H13.5"/></g></svg>www.kestrelofficeclearance.co.uk</li>
      </ul>
    </div>
  </section>

  <section class="card card-back">
    <div class="back-name">Kestrel Office Clearance</div>
    <div class="back-web">www.kestrelofficeclearance.co.uk</div>
  </section>
</body>
</html>
```